New Business Card Design Project LORVANTI-Italy

we are LORVANTI-Italy
our company in the market for 3 years we are luxury cosmetic company and its about time for a facelift :)
i will like to have elegant luxurious and unique business card
that will give the person that get it a unique, luxurious and elegant impression
I'm VERY OPEN FOR NEW IDEAS , even duo i add a few files of things that i see on line and i like them

i add my logo as well
my website is LORVANTI.COM
(if you would like to see the main style that we have)

Target Market(s)

adult that have money :)

Industry/Entity Type

Business

Contact Information for Business Card

Name - Dario Lorvanti
Position - CEO and CO Founder
address - 4817 E Halvern
telephone - 555-384-1926
email - dario@lorvanti.com
fax - 555-384-1926
website - LORVANTI.COM

Colors
000000
959595
fbee3e
ffffff

Requirements
Must have
• big logo in GOLD color
• elegant look
• impressive
Nice to have
• not must but maybe classy pattern background
• not must but maybe emblem
• maybe clear plastic business card
Should not have
• colors
• images

```html
<!DOCTYPE html>
<html lang="en">
<head>
<meta charset="utf-8">
<title>LORVANTI Italy – Business Card</title>
<link href="https://fonts.googleapis.com/css2?family=Cinzel:wght@400;500;600&family=PT+Sans:wght@400;700&display=swap" rel="stylesheet">
<style>
  :root {
    --stage: #e9e6e2;
    --card-black: #121212;
    --card-pattern: #1c1c1c;
    --gold: #e2b73c;
    --gold-soft: #d9ab35;
    --white: #f4f4f4;
    --shadow: rgba(0,0,0,0.28);
  }
  * { margin: 0; padding: 0; box-sizing: border-box; }
  html, body {
    width: 1200px; height: 900px; overflow: hidden;
    background: var(--stage);
  }
  .canvas { position: relative; width: 1200px; height: 900px; }

  .card {
    position: absolute;
    background: var(--card-black);
    box-shadow: 0 10px 30px var(--shadow);
    color: var(--white);
    text-align: center;
  }

  /* Contact side */
  .card--contact {
    left: 78px; top: 34px; width: 587px; height: 364px;
    font-family: "PT Sans", sans-serif;
  }
  .contact__name {
    position: absolute; left: 0; right: 0; top: 66px;
    font-family: "Cinzel", serif; font-weight: 600;
    font-size: 23px; line-height: 26px;
    color: var(--gold); letter-spacing: 0.3px;
  }
  .contact__role {
    position: absolute; left: 0; right: 0; top: 95px;
    font-size: 17px; line-height: 22px;
  }
  .contact__rule {
    position: absolute; left: 201px; width: 185px; top: 138px;
    height: 1px; background: var(--gold-soft); opacity: 0.8;
  }
  .contact__list {
    position: absolute; left: 0; right: 0; top: 163px;
    list-style: none; font-size: 16px; line-height: 23px;
  }
  .contact__label { color: var(--gold); font-weight: 700; }
  .contact__web { color: var(--gold); }
  .contact__address {
    position: absolute; left: 0; right: 0; top: 276px;
    font-size: 16px; line-height: 22px;
  }

  /* Brand side */
  .card--brand {
    left: 388px; top: 505px; width: 565px; height: 352px;
  }
  .brand__pattern {
    position: absolute; inset: 0;
    background: radial-gradient(ellipse at center, var(--card-pattern), var(--card-black));
  }
  .brand__mark {
    position: absolute; left: 222px; top: 51px; width: 116px; height: 116px;
  }
  .brand__name {
    position: absolute; left: 0; right: 0; top: 208px;
    font-family: "Cinzel", serif; font-weight: 500;
    font-size: 50px; line-height: 54px; color: var(--gold); letter-spacing: 1px;
  }
  .brand__rule {
    position: absolute; left: 142px; width: 282px; top: 270px;
    height: 3px; background: var(--gold);
  }
  .brand__country {
    position: absolute; left: 0; right: 0; top: 283px;
    font-family: "Cinzel", serif; font-weight: 400;
    font-size: 20px; line-height: 22px; color: var(--gold); letter-spacing: 1px;
  }
</style>
</head>
<body>
<main class="canvas">

  <section class="card card--contact">
    <h1 class="contact__name">DARIO LORVANTI</h1>
    <p class="contact__role">CEO and CO Founder</p>
    <div class="contact__rule"></div>
    <ul class="contact__list">
      <li><span class="contact__label">P:</span> 555-384-1926</li>
      <li><span class="contact__label">F:</span> 555-384-1926</li>
      <li><span class="contact__label">E:</span> dario@lorvanti.com</li>
      <li class="contact__web">www.lorvanti.com</li>
    </ul>
    <p class="contact__address">4817 E Halvern</p>
  </section>

  <section class="card card--brand">
    <div class="brand__pattern" role="img" aria-label="Subtle dark repeating pattern background"></div>
    <svg class="brand__mark" viewBox="0 0 116 116" aria-hidden="true">
      <circle cx="58" cy="58" r="55" fill="none" stroke="var(--gold)" stroke-width="4"/>
    </svg>
    <h2 class="brand__name">LORVANTI</h2>
    <div class="brand__rule"></div>
    <p class="brand__country">ITALY</p>
  </section>

</main>
</body>
</html>
```